Business Card Design

We need the business card for our new business based in St. Marys, we manufacture mainly bubble wraps. And we would like the design to use our company logo and also make it easy for people to understand right away we are bubble wrap manufacturer

Industry/Entity Type

Business

Contact Information for Business Card

Cushtane Pty Ltd, 14 Larkin Road Westbrook NSW 2794, Tel: 02 9471 5826, Fax: 9471 5839, Dara Oyelaran, General Manager, Mobile :0438 217 564, dara.oyelaran@cushtane.com.au, Website: cushtane.com.au

```html
<!DOCTYPE html>
<html lang="en">
<head>
<meta charset="utf-8">
<title>Cushtane Pty Ltd — Business Card</title>
<link href="https://fonts.googleapis.com/css2?family=Arimo:wght@400;700&display=swap" rel="stylesheet">
<style>
  :root {
    --backdrop: #e4e2de;
    --card: #f7f7f6;
    --brand-red: #b01e25;
    --ink: #1d1d1d;
    --ink-soft: #555555;
    --icon-box: #2a2a2a;
    --rule: #222222;
  }
  * { box-sizing: border-box; margin: 0; padding: 0; }
  html, body {
    width: 1200px; height: 901px; overflow: hidden;
    background: var(--backdrop);
  }
  .canvas {
    position: relative; width: 1200px; height: 901px;
    display: flex; flex-direction: column; align-items: center; justify-content: center; gap: 56px;
  }
  .card {
    position: relative; width: 560px; height: 342px;
    background: var(--card);
    box-shadow: 0 6px 18px rgba(0,0,0,.18);
    overflow: hidden;
    font-family: "Arimo", sans-serif;
  }
  .band-left {
    position: absolute; left: 0; top: 0; bottom: 0; width: 64px;
    background: var(--brand-red);
  }
  .band-right {
    position: absolute; right: 0; top: 0; bottom: 0; width: 26px;
    background: var(--brand-red);
  }

  /* Company name block */
  .company { display: flex; flex-direction: column; }
  .company-name {
    font-family: "Arimo", sans-serif; font-weight: 700;
    color: var(--ink); line-height: 1;
  }
  .company-line {
    font-family: "Arimo", sans-serif; font-weight: 400;
    color: var(--ink-soft);
  }

  /* Front */
  .card-front .company { position: absolute; left: 118px; top: 132px; }
  .card-front .company-name { font-size: 44px; }
  .card-front .company-line { font-size: 15px; margin-top: 12px; }

  /* Back */
  .card-back .band-left { width: 78px; }
  .card-back .company { position: absolute; right: 30px; top: 38px; align-items: flex-end; }
  .card-back .company-name { font-size: 32px; }
  .card-back .company-line { font-size: 12px; margin-top: 8px; }

  .person { position: absolute; left: 104px; top: 112px; }
  .person-name { font-size: 25px; font-weight: 400; color: var(--ink); }
  .person-title { font-size: 12px; color: var(--ink-soft); margin-top: 3px; }

  .rule {
    position: absolute; left: 104px; right: 30px; top: 174px;
    height: 1.5px; background: var(--rule);
  }
  .address {
    position: absolute; right: 30px; top: 130px; text-align: right;
    font-size: 13px; line-height: 1.35; color: var(--ink);
  }

  .contacts {
    position: absolute; left: 104px; top: 188px; list-style: none;
    font-size: 12.5px; color: var(--ink-soft);
  }
  .contacts li { display: flex; align-items: center; gap: 10px; height: 24px; }
  .contact-icon {
    width: 17px; height: 17px; background: var(--icon-box);
    display: flex; align-items: center; justify-content: center; flex: none;
  }
  .contact-icon svg { width: 11px; height: 11px; }
</style>
</head>
<body>
<main class="canvas">

  <section class="card card-front" aria-label="Card front">
    <div class="band-left"></div>
    <div class="band-right"></div>
    <div class="company">
      <div class="company-name">Cushtane</div>
      <div class="company-line">Bubble Wrap Manufacturers</div>
    </div>
  </section>

  <section class="card card-back" aria-label="Card back">
    <div class="band-left"></div>

    <div class="company">
      <div class="company-name">Cushtane</div>
      <div class="company-line">Bubble Wrap Manufacturers</div>
    </div>

    <div class="person">
      <div class="person-name">Dara Oyelaran</div>
      <div class="person-title">General Manager</div>
    </div>

    <div class="address">
      Cushtane Pty Ltd, 14 Larkin Road<br>
      Westbrook NSW 2794
    </div>

    <div class="rule"></div>

    <ul class="contacts">
      <li>
        <span class="contact-icon"><svg viewBox="0 0 12 12"><path d="M2.5 1 L4.5 1 L5 3.5 L3.8 4.4 Q5 7 7.6 8.2 L8.5 7 L11 7.5 L11 9.5 Q10.5 11 9 11 Q1 10 1 2.5 Q1 1.2 2.5 1 Z" fill="#d8333a"/></svg></span>
        <span>02 9471 5826</span>
      </li>
      <li>
        <span class="contact-icon"><svg viewBox="0 0 12 12"><rect x="3" y="0.5" width="6" height="11" rx="1" fill="#d8333a"/><rect x="4" y="2" width="4" height="6" fill="#2a2a2a"/></svg></span>
        <span>0438 217 564</span>
      </li>
      <li>
        <span class="contact-icon"><svg viewBox="0 0 12 12"><rect x="3" y="0.5" width="6" height="4" fill="#d8333a"/><rect x="0.5" y="4.5" width="11" height="5" rx="1" fill="#d8333a"/><rect x="3" y="8" width="6" height="3.5" fill="#d8333a" stroke="#2a2a2a" stroke-width=".6"/></svg></span>
        <span>9471 5839</span>
      </li>
      <li>
        <span class="contact-icon"><svg viewBox="0 0 12 12"><circle cx="6" cy="6" r="5" fill="none" stroke="#d8333a" stroke-width="1.3"/><path d="M1 6 H11 M6 1 Q3 6 6 11 M6 1 Q9 6 6 11" fill="none" stroke="#d8333a" stroke-width="1"/></svg></span>
        <span>www.cushtane.com.au</span>
      </li>
      <li>
        <span class="contact-icon"><svg viewBox="0 0 12 12"><rect x="0.5" y="2.5" width="11" height="7" fill="#d8333a"/><path d="M0.5 2.5 L6 7 L11.5 2.5" fill="none" stroke="#2a2a2a" stroke-width="1"/></svg></span>
        <span>dara.oyelaran@cushtane.com.au</span>
      </li>
    </ul>
  </section>

</main>
</body>
</html>
```